CrestHornSupply.com

I need a new webdesign for a company in the San Jose/SF Bay area that showcases the financial benefits of buying used band instruments for junior high students.This would be opposed to the current and costly option of renting cheap quality instruments from the 2 or 3 local music stores that charge a monthly fee that over the years charges the buyer 3 or 4x over..
Instruments: focus in on Alto Sax, Trumpet, Flute, Clarinet, Trombone, Tenor Sax, Baritone
Target middle schools are Larkfield Middle School and Maple Middle School in San Jose, CA. Both have award winning band programs.
Files attached may or may not be important.
Tabs Needed and funtional
Contact
Shopping Cart
Select Instrument
Checkout
Add to Cart, etc.
Instuments
quantity, etc.
trade in your instrument/sell your instrument
ability to add or take away new instruments for sale. including pictures
Additional questions or info, feel free to ask
Updates
Hi Designers,
Project Deadline Extended
Reason: In the next week you will be receiving specific content that will be required to be had on the website.
New desigins are still welcome. Please continue to contact me if you have questions about your individual designs.
Thanks!
Crest Horn

```html
<!DOCTYPE html>
<html lang="en">
<head>
<meta charset="utf-8">
<title>Crest Horn Instruments</title>
<link rel="stylesheet" href="https://fonts.googleapis.com/css2?family=Open+Sans:wght@400;600;700&display=swap">
<style>
:root{
  --gold:#e8b54a;
  --gold-light:#f3d27e;
  --red:#e10f0f;
  --ink:#1d1d1d;
  --text:#2c2c2c;
  --muted:#6a6a6a;
  --nav-top:#3a3a3a;
  --nav-bottom:#0e0e0e;
  --panel:#f0f0f0;
  --line:#cfcfcf;
  --green:#3da83d;
  --star:#f6a300;
}
*{box-sizing:border-box;margin:0;padding:0}
html,body{width:802px;height:1200px;overflow:hidden;background:#fff}
body{font-family:"Open Sans",Arial,sans-serif;color:var(--text)}
.page{position:relative;width:802px;height:1200px;background:linear-gradient(#f6f6f6,#fff 140px)}
.abs{position:absolute}

/* header */
.brand{left:115px;top:44px;display:flex;align-items:center;gap:8px}
.brand-dot{width:14px;height:14px;border-radius:50%;background:var(--gold);flex:none}
.brand-name{font-weight:700;font-size:20px;color:var(--ink);line-height:1.05;letter-spacing:.5px}
.brand-name small{display:block;font-size:13px;font-weight:700;letter-spacing:.3px}
.top-links{top:29px;left:339px;display:flex;font-size:7px;color:#333}
.top-links a{color:inherit;text-decoration:none;margin-right:18px}
.top-links .auth{color:var(--gold);margin-right:0}
.cart-icon{left:634px;top:16px}
.currency{left:670px;top:27px;font-size:9px;color:#555}
.phone{left:582px;top:54px;display:flex;align-items:center;gap:6px;color:var(--gold);font-size:15px}

/* nav */
.main-nav{left:115px;top:90px;width:572px;height:28px;background:linear-gradient(var(--nav-top),var(--nav-bottom));display:flex;align-items:center;box-shadow:0 4px 6px rgba(0,0,0,.15)}
.main-nav a{color:#fff;text-decoration:none;font-size:11px;font-weight:600;height:28px;line-height:28px;border-right:1px solid #4a4a4a;text-align:center}
.search{position:absolute;left:408px;top:4px;width:155px;height:20px;background:#fff;border-radius:3px;font-size:7px;color:#999;padding:6px 8px}
.search svg{position:absolute;right:8px;top:4px}

/* hero */
.hero{left:115px;top:133px;width:572px;height:244px;background:linear-gradient(#3f5a3a 0%,#b9211f 30%,#d9d4cf 55%,#9b3025 75%,#4a3a34 100%)}
.hero-caption{left:0;bottom:0;width:100%;height:40px;background:rgba(240,240,240,.88);font-size:10px;font-weight:700;color:#222;padding:13px 18px}
.hero-arrow{top:9px;width:20px;height:21px;background:#4a4a4a;display:flex;align-items:center;justify-content:center}

/* info cards */
.card{top:403px;width:177px;height:94px;background:linear-gradient(#fafafa 0,#fafafa 34px,#e2e2e2 34px,#4c4c4c 100%)}
.card-head{position:absolute;right:0;top:0;width:100%;height:34px;background:linear-gradient(90deg,#fafafa 15%,var(--gold-light) 32%,var(--gold) 100%);clip-path:polygon(25% 0,100% 0,100% 100%,0 100%,0 60%)}
.card-title{position:absolute;left:56px;top:7px;color:#fff;font-size:9px;line-height:1}
.card-title strong{display:block;font-size:13px;font-weight:600;text-align:right;width:78px;margin-top:1px}
.card-icon{position:absolute;left:6px;top:-6px}
.card-date{position:absolute;left:12px;top:40px;font-size:7px;font-style:italic;color:#222}
.card-body{position:absolute;left:12px;top:52px;width:158px;font-size:7px;line-height:10px;color:#fff}
.card-go{position:absolute;right:2px;bottom:-2px;width:18px;height:18px;border-radius:50%;background:#fff;display:flex;align-items:center;justify-content:center}
.teacher-thumbs{position:absolute;left:40px;top:33px;display:flex;gap:2px}
.teacher-thumbs span{width:14px;height:13px;background:linear-gradient(#c9a384,#6d5446)}

/* featured */
.section-bar{left:115px;top:525px;width:572px;height:28px;background:var(--panel);color:var(--gold);font-weight:700;font-size:11px;padding:7px 11px}
.product{width:130px}
.product-photo{width:130px;height:113px;border:1px solid #ddd;box-shadow:0 1px 2px rgba(0,0,0,.12);background:radial-gradient(ellipse at center,#e6c46a 0,#b98c2c 22%,#fff 45%)}
.product-photo.silver{background:radial-gradient(ellipse at center,#efeae0 0,#b9b3a4 22%,#fff 45%)}
.product-photo.dark{background:radial-gradient(ellipse at center,#3b3b3b 0,#111 20%,#fff 44%)}
.stars{margin:6px 0 0 1px;height:10px;display:flex;gap:1px}
.product-name{color:var(--red);font-weight:700;font-size:11px;margin-top:1px}
.product-desc{font-size:7px;line-height:10px;color:#333;margin:1px 0 0 2px}
.product-price{font-weight:700;font-size:11px;margin:5px 0 0 3px;color:#222}
.product-actions{display:flex;gap:4px;margin-top:4px}
.add-cart{width:70px;height:16px;background:linear-gradient(#3a3a3a,#101010);border-radius:2px;color:#fff;font-size:6.5px;font-weight:700;display:flex;align-items:center;gap:6px;padding-left:5px}
.mini-btn{width:15px;height:16px;border:1px solid #bbb;background:#fff;display:flex;align-items:center;justify-content:center}

/* footer */
.footer-rule{left:115px;width:572px;height:1px;background:var(--line)}
.footer-col{top:1102px}
.footer-col h4{color:var(--red);font-size:12px;font-weight:700;margin-bottom:4px}
.footer-col li{list-style:none;font-size:7px;line-height:13px;color:#333;padding-left:6px;position:relative}
.footer-col li::before{content:"";position:absolute;left:0;top:5px;width:3px;height:3px;background:var(--green)}
.footer-brand{left:570px;top:1124px;display:flex;align-items:center;gap:7px}
.footer-brand .brand-name{font-size:16px}
.footer-brand .brand-name small{font-size:11px}
.social{left:618px;top:1165px;display:flex;gap:6px}
.social span{width:12px;height:12px;border-radius:50%;background:#666}
</style>
</head>
<body>
<div class="page">

  <header>
    <div class="brand abs">
      <span class="brand-dot"></span>
      <div class="brand-name">CREST HORN<small>Instruments</small></div>
    </div>
    <nav class="top-links abs">
      <a href="#">Wish List (0)</a><a href="#">My Account</a><a href="#">Shopping Cart</a><a href="#">Checkout</a><a class="auth" href="#">Login &nbsp;|&nbsp; Register</a>
    </nav>
    <svg class="cart-icon abs" width="30" height="26" viewBox="0 0 30 26">
      <path d="M2 9h4l4 10h12l3-8H8" fill="none" stroke="#555" stroke-width="1.6"/>
      <circle cx="11" cy="22" r="2" fill="#555"/><circle cx="21" cy="22" r="2" fill="#555"/>
      <circle cx="19" cy="5" r="5" fill="var(--gold)"/>
      <text x="19" y="7.5" font-size="7" fill="#fff" text-anchor="middle" font-family="Open Sans,sans-serif">0</text>
    </svg>
    <div class="currency abs">$ &#8964;</div>
    <div class="phone abs">
      <svg width="14" height="14" viewBox="0 0 14 14"><circle cx="7" cy="7" r="6" fill="none" stroke="var(--gold)" stroke-width="1.5"/><path d="M7 3.5V7h2.5" fill="none" stroke="var(--gold)" stroke-width="1.5"/></svg>
      <span>408 55 01 27</span>
    </div>
  </header>

  <nav class="main-nav abs">
    <a href="#" style="width:61px">Home</a>
    <a href="#" style="width:80px">About Us</a>
    <a href="#" style="width:91px">Instruments</a>
    <a href="#" style="width:71px">Buy /Sell</a>
    <a href="#" style="width:91px;border-right:none">Contact Us</a>
    <div class="search">Search
      <svg width="12" height="12" viewBox="0 0 12 12"><circle cx="5" cy="5" r="3.8" fill="none" stroke="#222" stroke-width="1.6"/><path d="M8 8l3 3" stroke="#222" stroke-width="1.8"/></svg>
    </div>
  </nav>

  <section class="hero abs" role="img" aria-label="A school marching band in red and white uniforms performing outdoors">
    <div class="hero-caption abs">Donec arcu dolor, sodales ut lobortis adipiscing, auctor id purus.
      <span class="hero-arrow abs" style="left:502px"><svg width="7" height="10"><path d="M6 1L2 5l4 4" fill="none" stroke="#fff" stroke-width="1.3"/></svg></span>
      <span class="hero-arrow abs" style="left:525px"><svg width="7" height="10"><path d="M1 1l4 4-4 4" fill="none" stroke="#fff" stroke-width="1.3"/></svg></span>
    </div>
  </section>

  <article class="card abs" style="left:115px">
    <div class="card-head"></div>
    <svg class="card-icon" width="34" height="36" viewBox="0 0 34 36"><path d="M12 8l16-4v20" fill="none" stroke="#111" stroke-width="3"/><path d="M12 8v20" stroke="#111" stroke-width="3"/><ellipse cx="8" cy="29" rx="5" ry="4" fill="#111"/><ellipse cx="24" cy="25" rx="5" ry="4" fill="#111"/></svg>
    <div class="card-title">Music News &amp;<strong>EVENTS</strong></div>
    <div class="card-date">23-Jun-2014</div>
    <p class="card-body" style="top:52px">Nulla egestas mi non pulvinar sodales. Vesti bulum id luctus augue. Integer sem nisl, susc ipit sit amet cursus non, venenatis</p>
    <span class="card-go"><svg width="10" height="8"><path d="M0 4h6M5 1l3 3-3 3" fill="none" stroke="var(--gold)" stroke-width="2"/></svg></span>
  </article>

  <article class="card abs" style="left:312px">
    <div class="card-head"></div>
    <svg class="card-icon" width="34" height="36" viewBox="0 0 34 36"><path d="M20 14l10-10" stroke="#111" stroke-width="3"/><ellipse cx="13" cy="22" rx="9" ry="7" fill="#111" transform="rotate(-40 13 22)"/><circle cx="14" cy="21" r="2" fill="#fff"/></svg>
    <div class="card-title">Music Teachers<strong>AVAILABLE</strong></div>
    <div class="teacher-thumbs" role="img" aria-label="Small portraits of music teachers"><span></span><span></span><span></span><span></span><span></span></div>
    <p class="card-body" style="top:52px">Nulla egestas mi non pulvinar sodales. Vesti bulum id luctus augue. Integer sem nisl, susc ipit sit amet cursus non, venenatis</p>
    <span class="card-go"><svg width="10" height="8"><path d="M0 4h6M5 1l3 3-3 3" fill="none" stroke="var(--gold)" stroke-width="2"/></svg></span>
  </article>

  <article class="card abs" style="left:510px">
    <div class="card-head"></div>
    <svg class="card-icon" width="34" height="40" viewBox="0 0 34 40"><circle cx="18" cy="10" r="8" fill="#111"/><path d="M18 18v12q0 6-8 6" fill="none" stroke="#111" stroke-width="3"/></svg>
    <div class="card-title">Music Products<strong>HIGHLIGHTS</strong></div>
    <p class="card-body" style="top:42px">Nulla egestas mi non pulvinar sodales. Vesti bulum id luctus augue. Integer sem nisl, susc ipit sit amet cursus non, venenatis Praesent aliquet mauris ante,</p>
    <span class="card-go"><svg width="10" height="8"><path d="M0 4h6M5 1l3 3-3 3" fill="none" stroke="var(--gold)" stroke-width="2"/></svg></span>
  </article>

  <h2 class="section-bar abs">FEATURED PRODUCTS</h2>

  <div class="product abs" style="left:114px;top:593px">
    <div class="product-photo" role="img" aria-label="Alto saxophone"></div>
    <div class="stars"><svg width="60" height="10"><g fill="var(--star)"><path id="st" d="M5 0l1.5 3.3 3.5.3-2.7 2.3.9 3.5L5 7.5 1.8 9.4l.9-3.5L0 3.6l3.5-.3z"/><use href="#st" x="12"/><use href="#st" x="24"/></g><g fill="none" stroke="var(--star)" stroke-width=".8"><use href="#st" x="36"/><use href="#st" x="48"/></g></svg></div>
    <div class="product-name">Alto Sax</div>
    <p class="product-desc">vitae adipiscing urna accumsan vitae.<br>Nunc varius nunc ut nisl</p>
    <div class="product-price">$249.99</div>
    <div class="product-actions"><span class="add-cart"><svg width="13" height="10"><path d="M0 1h3l2 6h7l1-5H4" fill="var(--red)"/></svg>Add to Cart</span><span class="mini-btn"><svg width="8" height="7"><path d="M0 7V5h1.5v2zM2.5 7V3.5H4V7zM5 7V2h1.5v5zM7.2 7V0H8v7z" fill="var(--green)"/></svg></span><span class="mini-btn"><svg width="9" height="9"><path d="M4.5 0.5l1.2 2.7 2.9.3-2.2 1.9.7 2.9-2.6-1.6-2.6 1.6.7-2.9L.4 3.5l2.9-.3z" fill="none" stroke="var(--green)" stroke-width=".8"/></svg></span></div>
  </div>

  <div class="product abs" style="left:262px;top:593px">
    <div class="product-photo" role="img" aria-label="Trombone"></div>
    <div class="stars"><svg width="60" height="10"><g fill="var(--star)"><use href="#st"/><use href="#st" x="12"/><use href="#st" x="24"/></g><g fill="none" stroke="var(--star)" stroke-width=".8"><use href="#st" x="36"/><use href="#st" x="48"/></g></svg></div>
    <div class="product-name">Trombone</div>
    <p class="product-desc">vitae adipiscing urna accumsan vitae.<br>Nunc varius nunc ut nisl</p>
    <div class="product-price">$249.99</div>
    <div class="product-actions"><span class="add-cart"><svg width="13" height="10"><path d="M0 1h3l2 6h7l1-5H4" fill="var(--red)"/></svg>Add to Cart</span><span class="mini-btn"><svg width="8" height="7"><path d="M0 7V5h1.5v2zM2.5 7V3.5H4V7zM5 7V2h1.5v5zM7.2 7V0H8v7z" fill="var(--green)"/></svg></span><span class="mini-btn"><svg width="9" height="9"><path d="M4.5 0.5l1.2 2.7 2.9.3-2.2 1.9.7 2.9-2.6-1.6-2.6 1.6.7-2.9L.4 3.5l2.9-.3z" fill="none" stroke="var(--green)" stroke-width=".8"/></svg></span></div>
  </div>

  <div class="product abs" style="left:410px;top:593px">
    <div class="product-photo dark" role="img" aria-label="Clarinet"></div>
    <div class="stars"><svg width="60" height="10"><g fill="var(--star)"><use href="#st"/><use href="#st" x="12"/><use href="#st" x="24"/></g><g fill="none" stroke="var(--star)" stroke-width=".8"><use href="#st" x="36"/><use href="#st" x="48"/></g></svg></div>
    <div class="product-name">Clarinet</div>
    <p class="product-desc">vitae adipiscing urna accumsan vitae.<br>Nunc varius nunc ut nisl</p>
    <div class="product-price">$249.99</div>
    <div class="product-actions"><span class="add-cart"><svg width="13" height="10"><path d="M0 1h3l2 6h7l1-5H4" fill="var(--red)"/></svg>Add to Cart</span><span class="mini-btn"><svg width="8" height="7"><path d="M0 7V5h1.5v2zM2.5 7V3.5H4V7zM5 7V2h1.5v5zM7.2 7V0H8v7z" fill="var(--green)"/></svg></span><span class="mini-btn"><svg width="9" height="9"><path d="M4.5 0.5l1.2 2.7 2.9.3-2.2 1.9.7 2.9-2.6-1.6-2.6 1.6.7-2.9L.4 3.5l2.9-.3z" fill="none" stroke="var(--green)" stroke-width=".8"/></svg></span></div>
  </div>

  <div class="product abs" style="left:558px;top:593px">
    <div class="product-photo silver" role="img" aria-label="Flute"></div>
    <div class="stars"><svg width="60" height="10"><g fill="var(--star)"><use href="#st"/><use href="#st" x="12"/><use href="#st" x="24"/></g><g fill="none" stroke="var(--star)" stroke-width=".8"><use href="#st" x="36"/><use href="#st" x="48"/></g></svg></div>
    <div class="product-name">Flute</div>
    <p class="product-desc">vitae adipiscing urna accumsan vitae.<br>Nunc varius nunc ut nisl</p>
    <div class="product-price">$249.99</div>
    <div class="product-actions"><span class="add-cart"><svg width="13" height="10"><path d="M0 1h3l2 6h7l1-5H4" fill="var(--red)"/></svg>Add to Cart</span><span class="mini-btn"><svg width="8" height="7"><path d="M0 7V5h1.5v2zM2.5 7V3.5H4V7zM5 7V2h1.5v5zM7.2 7V0H8v7z" fill="var(--green)"/></svg></span><span class="mini-btn"><svg width="9" height="9"><path d="M4.5 0.5l1.2 2.7 2.9.3-2.2 1.9.7 2.9-2.6-1.6-2.6 1.6.7-2.9L.4 3.5l2.9-.3z" fill="none" stroke="var(--green)" stroke-width=".8"/></svg></span></div>
  </div>

  <div class="product abs" style="left:114px;top:840px">
    <div class="product-photo" role="img" aria-label="Baritone horn"></div>
    <div class="stars"><svg width="60" height="10"><g fill="var(--star)"><use href="#st"/><use href="#st" x="12"/><use href="#st" x="24"/></g><g fill="none" stroke="var(--star)" stroke-width=".8"><use href="#st" x="36"/><use href="#st" x="48"/></g></svg></div>
    <div class="product-name">Baritone</div>
    <p class="product-desc">vitae adipiscing urna accumsan vitae.<br>Nunc varius nunc ut nisl</p>
    <div class="product-price">$249.99</div>
    <div class="product-actions"><span class="add-cart"><svg width="13" height="10"><path d="M0 1h3l2 6h7l1-5H4" fill="var(--red)"/></svg>Add to Cart</span><span class="mini-btn"><svg width="8" height="7"><path d="M0 7V5h1.5v2zM2.5 7V3.5H4V7zM5 7V2h1.5v5zM7.2 7V0H8v7z" fill="var(--green)"/></svg></span><span class="mini-btn"><svg width="9" height="9"><path d="M4.5 0.5l1.2 2.7 2.9.3-2.2 1.9.7 2.9-2.6-1.6-2.6 1.6.7-2.9L.4 3.5l2.9-.3z" fill="none" stroke="var(--green)" stroke-width=".8"/></svg></span></div>
  </div>

  <div class="product abs" style="left:262px;top:840px">
    <div class="product-photo" role="img" aria-label="Trumpet"></div>
    <div class="stars"><svg width="60" height="10"><g fill="var(--star)"><use href="#st"/><use href="#st" x="12"/><use href="#st" x="24"/></g><g fill="none" stroke="var(--star)" stroke-width=".8"><use href="#st" x="36"/><use href="#st" x="48"/></g></svg></div>
    <div class="product-name">Trumpet</div>
    <p class="product-desc">vitae adipiscing urna accumsan vitae.<br>Nunc varius nunc ut nisl</p>
    <div class="product-price">$249.99</div>
    <div class="product-actions"><span class="add-cart"><svg width="13" height="10"><path d="M0 1h3l2 6h7l1-5H4" fill="var(--red)"/></svg>Add to Cart</span><span class="mini-btn"><svg width="8" height="7"><path d="M0 7V5h1.5v2zM2.5 7V3.5H4V7zM5 7V2h1.5v5zM7.2 7V0H8v7z" fill="var(--green)"/></svg></span><span class="mini-btn"><svg width="9" height="9"><path d="M4.5 0.5l1.2 2.7 2.9.3-2.2 1.9.7 2.9-2.6-1.6-2.6 1.6.7-2.9L.4 3.5l2.9-.3z" fill="none" stroke="var(--green)" stroke-width=".8"/></svg></span></div>
  </div>

  <div class="product abs" style="left:410px;top:840px">
    <div class="product-photo" role="img" aria-label="Tenor saxophone"></div>
    <div class="stars"><svg width="60" height="10"><g fill="var(--star)"><use href="#st"/><use href="#st" x="12"/><use href="#st" x="24"/></g><g fill="none" stroke="var(--star)" stroke-width=".8"><use href="#st" x="36"/><use href="#st" x="48"/></g></svg></div>
    <div class="product-name">Tenor Sax</div>
    <p class="product-desc">vitae adipiscing urna accumsan vitae.<br>Nunc varius nunc ut nisl</p>
    <div class="product-price">$249.99</div>
    <div class="product-actions"><span class="add-cart"><svg width="13" height="10"><path d="M0 1h3l2 6h7l1-5H4" fill="var(--red)"/></svg>Add to Cart</span><span class="mini-btn"><svg width="8" height="7"><path d="M0 7V5h1.5v2zM2.5 7V3.5H4V7zM5 7V2h1.5v5zM7.2 7V0H8v7z" fill="var(--green)"/></svg></span><span class="mini-btn"><svg width="9" height="9"><path d="M4.5 0.5l1.2 2.7 2.9.3-2.2 1.9.7 2.9-2.6-1.6-2.6 1.6.7-2.9L.4 3.5l2.9-.3z" fill="none" stroke="var(--green)" stroke-width=".8"/></svg></span></div>
  </div>

  <div class="product abs" style="left:558px;top:840px">
    <div class="product-photo" role="img" aria-label="Trumpet"></div>
    <div class="stars"><svg width="60" height="10"><g fill="var(--star)"><use href="#st"/><use href="#st" x="12"/><use href="#st" x="24"/></g><g fill="none" stroke="var(--star)" stroke-width=".8"><use href="#st" x="36"/><use href="#st" x="48"/></g></svg></div>
    <div class="product-name">Trumpet</div>
    <p class="product-desc">vitae adipiscing urna accumsan vitae.<br>Nunc varius nunc ut nisl</p>
    <div class="product-price">$249.99</div>
    <div class="product-actions"><span class="add-cart"><svg width="13" height="10"><path d="M0 1h3l2 6h7l1-5H4" fill="var(--red)"/></svg>Add to Cart</span><span class="mini-btn"><svg width="8" height="7"><path d="M0 7V5h1.5v2zM2.5 7V3.5H4V7zM5 7V2h1.5v5zM7.2 7V0H8v7z" fill="var(--green)"/></svg></span><span class="mini-btn"><svg width="9" height="9"><path d="M4.5 0.5l1.2 2.7 2.9.3-2.2 1.9.7 2.9-2.6-1.6-2.6 1.6.7-2.9L.4 3.5l2.9-.3z" fill="none" stroke="var(--green)" stroke-width=".8"/></svg></span></div>
  </div>

  <footer>
    <div class="footer-rule abs" style="top:1089px"></div>
    <div class="footer-col abs" style="left:117px"><h4>Information</h4><ul><li>About</li><li>Delivery</li><li>Privacy Policy</li><li>Terms &amp; Conditions</li></ul></div>
    <div class="footer-col abs" style="left:215px"><h4>Customer Service</h4><ul><li>Contact Us</li><li>Returns</li><li>Site Map</li></ul></div>
    <div class="footer-col abs" style="left:347px"><h4>Extras</h4><ul><li>Brands</li><li>Gift Vouchers</li><li>Affiliates</li><li>Specials</li></ul></div>
    <div class="footer-col abs" style="left:428px"><h4>My Account</h4><ul><li>My Account</li><li>Order History</li><li>Wish List</li><li>Newsletter</li></ul></div>
    <div class="footer-brand abs">
      <span class="brand-dot"></span>
      <div class="brand-name">CREST HORN<small>Instruments</small></div>
    </div>
    <div class="social abs"><span></span><span></span><span></span><span></span></div>
    <div class="footer-rule abs" style="top:1196px"></div>
  </footer>

</div>
</body>
</html>
```